Shine Fox Auto Care Business Card

2 side business card design for an auto detailing business

Target Market(s)

Auto detailing

Contact Information for Business Card

Things included

The business name “Shine Fox Auto Care”
Mark Dunrow
(403)271-6094
Corrin Falls, Sk

Services offered - complete interior& exterior detail
- paint correction & protection
- ceramic coating
- trim restore
- auto carpet & seat cleaning

Requirements
Must have
• Colours that are in my logo

Services offered

My name Mark Dunrow
403-271-6094
Corrin Falls, Sk

Not too sure in what order for these ?
Website. Shinefoxautocare.com
Instagram Shinefoxautocare
Email. Shinefoxautoac@mailvento.com

```html
<!DOCTYPE html>
<html lang="en">
<head>
<meta charset="utf-8">
<title>Shine Fox Auto Care — Business Card</title>
<link rel="stylesheet" href="https://fonts.googleapis.com/css2?family=Michroma&family=Montserrat:wght@400;500;700&display=swap">
<style>
  :root {
    --brand-red: #980000;
    --ink: #111111;
    --text-grey: #4a4a4a;
    --paper: #ffffff;
    --backdrop: #e9e9e9;
  }
  * { margin: 0; padding: 0; box-sizing: border-box; }
  html, body { width: 1200px; height: 1200px; overflow: hidden; }
  body { background: var(--backdrop); position: relative; font-family: "Montserrat", sans-serif; }

  .card {
    position: absolute; left: 200px; width: 800px; height: 457px;
    border-radius: 26px; overflow: hidden;
  }
  .card--front { top: 87px; background: var(--paper); }
  .card--back { top: 656px; background: var(--brand-red); color: var(--paper); }

  .brand-name { font-family: "Michroma", sans-serif; font-weight: 400; white-space: nowrap; }
  .brand-name .brand-title { display: block; line-height: 1; }
  .brand-name .brand-sub { display: block; line-height: 1; }

  .card--front .brand-name { position: absolute; left: 50px; top: 72px; }
  .card--front .brand-title { font-size: 31px; color: var(--ink); }
  .card--front .brand-sub { font-size: 16px; letter-spacing: 12.2px; color: var(--brand-red); margin-top: 4px; }

  .holder-name {
    position: absolute; left: 50px; top: 260px;
    font-family: "Michroma", sans-serif; font-size: 25px; line-height: 1; color: var(--brand-red);
  }
  .contact-list { position: absolute; left: 50px; top: 310px; list-style: none; }
  .contact-list li {
    display: flex; align-items: center; gap: 15px;
    font-size: 18px; color: var(--text-grey); height: 22.5px; white-space: nowrap;
  }
  .contact-list li.location { margin-bottom: 14px; }
  .contact-list svg { width: 16px; height: 16px; fill: var(--brand-red); flex: none; }

  .brand-ring { position: absolute; left: 347px; top: 12px; width: 434px; height: 434px; }

  .back-ring { position: absolute; left: 343px; top: 116px; width: 114px; height: 114px; }
  .card--back .brand-name { position: absolute; left: 0; right: 0; top: 246px; text-align: center; }
  .card--back .brand-title { font-size: 37px; }
  .card--back .brand-sub { font-size: 19px; letter-spacing: 17px; margin-left: 17px; margin-top: 7px; }
  .services-title {
    position: absolute; left: 0; right: 0; top: 340px; text-align: center;
    font-weight: 700; font-size: 18px; line-height: 22px; letter-spacing: 0.3px;
  }
  .services-list {
    position: absolute; left: 0; right: 0; top: 369px; text-align: center;
    font-size: 18.5px; line-height: 23.5px; letter-spacing: 0.4px;
  }
  .services-list .dot { display: inline-block; width: 7px; height: 7px; border-radius: 50%; background: var(--paper); vertical-align: middle; margin: 0 8px 3px; }
</style>
</head>
<body>
  <section class="card card--front">
    <div class="brand-name"><span class="brand-title">SHINE FOX</span><span class="brand-sub">AUTO CARE</span></div>
    <div class="holder-name">MARK DUNROW</div>
    <ul class="contact-list">
      <li class="location"><svg viewBox="0 0 16 16"><path d="M8 0a6 6 0 0 0-6 6c0 4.5 6 10 6 10s6-5.5 6-10a6 6 0 0 0-6-6zm0 8.5A2.5 2.5 0 1 1 8 3.5a2.5 2.5 0 0 1 0 5z"/></svg>Corrin Falls, Sk</li>
      <li><svg viewBox="0 0 16 16"><path d="M3.6 1l2.6 3-1.6 1.8c.9 2 2.6 3.7 4.6 4.6L11 8.8l3 2.6-1.4 2.6C7 14.4 1.6 9 2 3.4z"/></svg>(403)271-6094</li>
      <li><svg viewBox="0 0 16 16"><path d="M1 3h14v10H1zm1.5 1.2L8 8.6l5.5-4.4z"/></svg>info@shinefoxautocare.com</li>
      <li><svg viewBox="0 0 16 16"><path d="M8 1a7 7 0 1 0 0 14A7 7 0 0 0 8 1zm0 2.2c1 0 1.6 2.2 1.6 4.8S9 12.8 8 12.8 6.4 10.6 6.4 8 7 3.2 8 3.2zM2.6 7.3h11v1.4h-11z"/></svg>www.shinefoxautocare.com</li>
    </ul>
    <svg class="brand-ring" viewBox="0 0 434 434" aria-hidden="true">
      <circle cx="217" cy="217" r="201" fill="none" stroke="var(--brand-red)" stroke-width="30"/>
    </svg>
  </section>

  <section class="card card--back">
    <svg class="back-ring" viewBox="0 0 114 114" aria-hidden="true">
      <circle cx="57" cy="57" r="52" fill="none" stroke="var(--paper)" stroke-width="9"/>
    </svg>
    <div class="brand-name"><span class="brand-title">SHINE FOX</span><span class="brand-sub">AUTO CARE</span></div>
    <div class="services-title">COMPLETE INTERIOR &amp; EXTERIOR DETAIL</div>
    <div class="services-list">
      Paint correction &amp; Protection<span class="dot"></span>Ceramic coating<br>
      Trim restore<span class="dot"></span>Auto carpet &amp; Seat cleaning
    </div>
  </section>
</body>
</html>
```